Brellwick Partners, LLC Stationary

Brellwick Partners, LLC is a new financial planning and consulting company. We are looking for designs on business cards, letterhead, envelopes, and anything else that would be useful. Our preference for business card design is two sided. We are looking for a professional and clean look with incorporating the logo and patriotic feel. Thank you to all who participate and good luck!

```html
<!DOCTYPE html>
<html lang="en">
<head>
<meta charset="utf-8">
<title>Brellwick Partners, LLC Stationery</title>
<link rel="stylesheet" href="https://fonts.googleapis.com/css2?family=Montserrat:wght@400;600&display=swap">
<style>
  :root {
    --navy: #1f4369;
    --navy-deep: #0d365e;
    --red: #c8282e;
    --paper: #f4f4f4;
    --backdrop: #e6e6e6;
    --ink: #6a6a6a;
  }
  html, body { margin: 0; padding: 0; overflow: hidden; }
  body {
    width: 1200px; height: 821px; position: relative;
    background: var(--backdrop);
    font-family: "Montserrat", Arial, sans-serif;
  }
  .sheet { position: absolute; background: var(--paper); box-shadow: 0 2px 6px rgba(0,0,0,0.12); }
  .side-band {
    position: absolute; top: 0; bottom: 0; left: 0;
    background: var(--navy); border-right: 2px solid var(--red);
  }
  .side-band::after {
    content: ""; position: absolute; top: 0; bottom: 0; right: -4px;
    width: 2px; background: var(--paper);
  }
  .brand { position: absolute; }
  .brand-name {
    color: var(--navy); font-weight: 600; white-space: nowrap;
    letter-spacing: 0.02em; margin: 0;
  }
  .brand-tagline {
    color: var(--red); font-weight: 400; white-space: nowrap;
    letter-spacing: 0.12em; margin: 2px 0 0; text-transform: uppercase;
  }

  .letterhead { left: 69px; top: 110px; width: 467px; height: 661px; }
  .letterhead .side-band { width: 33px; }
  .letterhead .brand { left: 58px; top: 50px; }
  .letterhead .brand-name { font-size: 16px; }
  .letterhead .brand-tagline { font-size: 5px; }
  .letterhead-footer {
    position: absolute; left: 33px; right: 0; bottom: 22px;
    text-align: center; color: var(--ink); font-size: 7px; line-height: 11px;
  }
  .letterhead-footer b { color: var(--navy); font-weight: 600; }

  .envelope-front { left: 614px; top: 224px; width: 522px; height: 250px; }
  .envelope-front .side-band { width: 30px; }
  .envelope-front .brand { left: 55px; top: 37px; }
  .envelope-front .brand-name { font-size: 13px; }
  .envelope-front .brand-tagline { font-size: 4px; }
  .return-address {
    position: absolute; left: 57px; top: 64px;
    color: var(--ink); font-size: 7.5px; line-height: 10px; margin: 0;
  }

  .envelope-back { left: 619px; top: 515px; width: 523px; height: 247px; }
  .flap {
    position: absolute; left: 0; right: 0; top: 0; height: 87px;
    background: var(--navy-deep);
    border-radius: 0 0 12px 12px;
    margin: 0 10px;
  }
  .flap-mark {
    position: absolute; left: 50%; top: 50%; width: 22px; height: 22px;
    margin: -11px 0 0 -11px; border-radius: 50%; background: var(--paper);
  }
</style>
</head>
<body>
  <section class="sheet letterhead">
    <div class="side-band"></div>
    <div class="brand">
      <p class="brand-name">Brellwick Partners, LLC</p>
      <p class="brand-tagline">Financial Planning and Consulting</p>
    </div>
    <footer class="letterhead-footer">
      412 Harlow Street, Juneau, Alaska 99801<br>
      <b>P :</b> 555 210 4417 &nbsp;<b>F :</b> 555 210 4418 &nbsp;<b>E :</b> hello@brellwick.com &nbsp;<b>W :</b> www.brellwick.com
    </footer>
  </section>

  <section class="sheet envelope-front">
    <div class="side-band"></div>
    <div class="brand">
      <p class="brand-name">Brellwick Partners, LLC</p>
      <p class="brand-tagline">Financial Planning and Consulting</p>
    </div>
    <p class="return-address">412 Harlow Street<br>Juneau, Alaska 99801</p>
  </section>

  <section class="sheet envelope-back">
    <div class="flap"><span class="flap-mark"></span></div>
  </section>
</body>
</html>
```